Veldmark Supplies Business Card

Professional business card that stand out to our potential customers. Front and back with clean modern design

Industry/Entity Type

Oil and gas

Contact Information for Business Card

Name, address, website , office phone and cell number

Requirements
Must have
• Editable files for each employee

```html
<!DOCTYPE html>
<html lang="en">
<head>
<meta charset="utf-8">
<title>Veldmark Supplies Business Card</title>
<link href="https://fonts.googleapis.com/css2?family=Montserrat:wght@400;500;700&display=swap" rel="stylesheet">
<style>
  :root {
    --backdrop: #d1d6d7;
    --paper: #f1f1f0;
    --brand-red: #e8242b;
    --brand-blue: #14b2d3;
    --ink: #2a2a2a;
    --ink-soft: #4a4a4a;
  }
  * { box-sizing: border-box; margin: 0; padding: 0; }
  html, body { width: 1200px; height: 881px; overflow: hidden; }
  body {
    background: var(--backdrop);
    font-family: "Montserrat", sans-serif;
    position: relative;
  }
  .card {
    position: absolute;
    top: 292px;
    width: 530px;
    height: 303px;
    background: var(--paper);
    border-bottom: 5px solid var(--brand-red);
    box-shadow: 0 18px 40px rgba(0,0,0,0.18);
  }
  .card--front { left: 40px; }
  .card--back { left: 630px; }

  .wordmark {
    display: flex;
    align-items: center;
    gap: 10px;
    color: var(--brand-red);
    font-weight: 700;
    text-transform: uppercase;
    letter-spacing: 0.06em;
    white-space: nowrap;
  }
  .wordmark__mark {
    background: var(--brand-red);
    flex: none;
  }
  .card--front .wordmark {
    position: absolute;
    left: 240px;
    top: 40px;
    font-size: 17px;
  }
  .card--front .wordmark__mark { width: 18px; height: 18px; }

  .card--back .wordmark {
    position: absolute;
    left: 50%;
    top: 50%;
    transform: translate(-50%, -50%);
    font-size: 30px;
    gap: 16px;
  }
  .card--back .wordmark__mark { width: 30px; height: 30px; }

  .holder {
    position: absolute;
    left: 40px;
    top: 112px;
    width: 210px;
    text-align: right;
  }
  .holder__name {
    font-size: 25px;
    font-weight: 500;
    letter-spacing: 0.01em;
    color: var(--brand-red);
  }
  .holder__surname { color: var(--brand-blue); }
  .holder__title {
    margin-top: 4px;
    font-size: 13px;
    color: var(--ink-soft);
    letter-spacing: 0.03em;
  }

  .divider {
    position: absolute;
    left: 268px;
    top: 112px;
    width: 2px;
    height: 100px;
    background: var(--brand-red);
  }

  .contacts {
    position: absolute;
    left: 284px;
    top: 116px;
    list-style: none;
    font-size: 12.5px;
    color: var(--ink);
  }
  .contacts li {
    display: flex;
    align-items: center;
    gap: 8px;
    height: 23px;
  }
  .contacts svg { width: 12px; height: 12px; fill: var(--brand-red); flex: none; }

  .address {
    position: absolute;
    left: 40px;
    right: 40px;
    bottom: 36px;
    font-size: 12.5px;
    color: var(--ink);
    letter-spacing: 0.02em;
  }
</style>
</head>
<body>

<section class="card card--front" aria-label="Business card front">
  <div class="wordmark"><span class="wordmark__mark"></span>Veldmark Supplies</div>

  <div class="holder">
    <p class="holder__name">DANIEL <span class="holder__surname">REYES</span></p>
    <p class="holder__title">Managing Director</p>
  </div>

  <div class="divider"></div>

  <ul class="contacts">
    <li>
      <svg viewBox="0 0 24 24" aria-hidden="true"><path d="M3 9c0-3 4-5 9-5s9 2 9 5l-3 2-3-2V7H9v2l-3 2zM5 13h14l1 7H4z"/></svg>
      (555)214-0387
    </li>
    <li>
      <svg viewBox="0 0 24 24" aria-hidden="true"><path d="M7 1h10a2 2 0 0 1 2 2v18a2 2 0 0 1-2 2H7a2 2 0 0 1-2-2V3a2 2 0 0 1 2-2zm0 3v15h10V4zm5 16.2a1 1 0 1 0 0 .1z"/></svg>
      987 654 321
    </li>
    <li>
      <svg viewBox="0 0 24 24" aria-hidden="true"><path d="M2 5h20v14H2zm2 2v.4l8 5.6 8-5.6V7l-8 5.5z"/></svg>
      sales@veldmarksupplies.com
    </li>
    <li>
      <svg viewBox="0 0 24 24" aria-hidden="true"><path d="M12 2a10 10 0 1 0 0 20 10 10 0 0 0 0-20zm-1 17.9A8 8 0 0 1 4.2 10L9 15v1a2 2 0 0 0 2 2zm6.9-2.5A2 2 0 0 0 16 16h-1v-3a1 1 0 0 0-1-1H8v-2h2a1 1 0 0 0 1-1V7h2a2 2 0 0 0 2-2v-.4a8 8 0 0 1 2.9 12.8z"/></svg>
      www.veldmarksupplies.com
    </li>
  </ul>

  <p class="address">412 N.Harlow Suite 7 Midland, Tx 79701</p>
</section>

<section class="card card--back" aria-label="Business card back">
  <div class="wordmark"><span class="wordmark__mark"></span>Veldmark Supplies</div>
</section>

</body>
</html>
```